The Brandwell Firm

We need a new design for our letterhead and envelopes. We are a personal injury and criminal defense firm so we need something modern and clean, but more on the professional/traditional side. Our new logo has two colors and is attached to the file so we need something that works well with those colors/matches the design. The following information needs to be on the letterhead:
Phone: (555) 214-3370
Fax: (555) 214-5186
Toll-Free: (888) 431-2059
Post Office Box 4721
Millbrook, SC 29555-4721
HarmClaimCounsel.example
PalmettoTrialAdvocates.example

Target Market(s)

Clients, government agencies, other law firms

Industry/Entity Type

Legal

Font styles to use
Sans Serif
Other font styles liked:
• Arial

Colors

Designer to choose colors to be used in the design.

Requirements
Must have
• Must look professional and clean, modern
Nice to have
• I would like to see a design that works with the logo but does not distract from the content that will be printed on it
Should not have
• Too many colors or crazy designs.

```html
<!DOCTYPE html>
<html lang="en">
<head>
<meta charset="utf-8">
<title>The Brandwell Firm – Stationery</title>
<link rel="stylesheet" href="https://fonts.googleapis.com/css2?family=Open+Sans:wght@400;600&display=swap">
<style>
  :root {
    --firm-blue: #2e3192;
    --firm-red: #d71f27;
    --paper: #ffffff;
    --backdrop: #eeeeee;
    --ink: #333333;
    --edge: #dddddd;
  }
  * { box-sizing: border-box; margin: 0; padding: 0; }
  html, body { width: 1155px; height: 1200px; overflow: hidden; }
  body {
    background: var(--backdrop);
    font-family: "Open Sans", Arial, sans-serif;
    color: var(--ink);
    position: relative;
  }
  .sheet {
    position: absolute;
    background: var(--paper);
    border: 1px solid var(--edge);
    overflow: hidden;
  }
  .letterhead { left: 98px; top: 236px; width: 543px; height: 715px; }
  .envelope-back { left: 542px; top: 377px; width: 552px; height: 253px; }
  .envelope-front { left: 542px; top: 661px; width: 552px; height: 253px; }

  .brand {
    position: absolute;
    display: flex;
    align-items: center;
    gap: 8px;
  }
  .brand-mark {
    width: 12px; height: 12px;
    background: var(--firm-red);
  }
  .brand-name {
    font-weight: 600;
    font-size: 20px;
    line-height: 1;
    color: var(--firm-blue);
    letter-spacing: 0.2px;
  }
  .letterhead .brand { left: 36px; top: 90px; }
  .envelope-front .brand { left: 24px; top: 67px; }

  .contact {
    position: absolute;
    font-size: 7.6px;
    line-height: 10.2px;
  }
  .letterhead .contact {
    left: 375px; top: 46px;
    padding-left: 11px;
    border-left: 1px solid var(--firm-blue);
  }
  .envelope-front .contact { left: 22px; top: 169px; }
  .contact .address { margin-bottom: 3px; }
  .contact li {
    list-style: none;
    display: flex;
    align-items: center;
    gap: 4px;
  }
  .contact svg { width: 7px; height: 7px; flex: none; fill: none; stroke: var(--firm-red); stroke-width: 1.4; }
  .contact svg.solid { fill: var(--firm-red); stroke: none; }

  .stripe {
    position: absolute;
    left: 0; bottom: 0;
    width: 100%;
  }
  .letterhead .stripe { height: 14px; }
  .envelope-front .stripe { height: 13px; }

  .flap { position: absolute; left: 0; top: 0; width: 552px; height: 71px; }
  .flap-seal {
    position: absolute;
    left: 270px; top: 29px;
    width: 12px; height: 12px;
    border-radius: 50%;
    background: var(--paper);
  }
</style>
</head>
<body>

<svg width="0" height="0" style="position:absolute" aria-hidden="true">
  <defs>
    <symbol id="icon-phone" viewBox="0 0 10 10">
      <path d="M2 1 L3.6 1 L4.2 3.2 L3.2 4 Q4 6 6 6.8 L6.8 5.8 L9 6.4 L9 8 Q9 9 8 9 Q1 8.6 1 2 Q1 1 2 1 Z" fill="currentColor" stroke="none"/>
    </symbol>
    <symbol id="icon-fax" viewBox="0 0 10 10">
      <path d="M2.5 1 H7.5 V3.5 H2.5 Z M1 3.5 H9 V7.5 H1 Z M2.5 6 H7.5 V9 H2.5 Z" fill="currentColor" stroke="none"/>
    </symbol>
    <symbol id="icon-web" viewBox="0 0 10 10">
      <circle cx="5" cy="5" r="4"/>
      <path d="M1 5 H9 M5 1 Q2.5 5 5 9 M5 1 Q7.5 5 5 9"/>
    </symbol>
  </defs>
</svg>

<!-- Letterhead -->
<section class="sheet letterhead">
  <div class="brand">
    <span class="brand-mark"></span>
    <span class="brand-name">The Brandwell Firm</span>
  </div>
  <div class="contact">
    <p class="address">P.O. Box 4721 Millbrook,<br>SC 29555-4721</p>
    <ul>
      <li><svg class="solid" style="color:var(--firm-red)"><use href="#icon-phone"/></svg>(555) 214-3370</li>
      <li><svg class="solid" style="color:var(--firm-red)"><use href="#icon-fax"/></svg>(555) 214-5186</li>
      <li><svg class="solid" style="color:var(--firm-red)"><use href="#icon-phone"/></svg>(888) 431-2059 (Toll-Free)</li>
      <li><svg><use href="#icon-web"/></svg>HarmClaimCounsel.example</li>
      <li><svg><use href="#icon-web"/></svg>PalmettoTrialAdvocates.example</li>
    </ul>
  </div>
  <svg class="stripe" viewBox="0 0 543 14" preserveAspectRatio="none" aria-hidden="true">
    <polygon points="0,0 374,0 360,14 0,14" fill="var(--firm-blue)"/>
    <polygon points="374,0 543,0 543,14 360,14" fill="var(--firm-red)"/>
  </svg>
</section>

<!-- Envelope, back with flap -->
<section class="sheet envelope-back">
  <svg class="flap" viewBox="0 0 552 71" aria-hidden="true">
    <path d="M0,0 H552 L542,52 Q538,70 520,70 H32 Q14,70 10,52 Z" fill="var(--firm-blue)"/>
  </svg>
  <span class="flap-seal"></span>
</section>

<!-- Envelope, front -->
<section class="sheet envelope-front">
  <div class="brand">
    <span class="brand-mark"></span>
    <span class="brand-name">The Brandwell Firm</span>
  </div>
  <div class="contact">
    <p class="address">P.O. Box 4721 Millbrook,<br>SC 29555-4721</p>
    <ul>
      <li><svg class="solid" style="color:var(--firm-red)"><use href="#icon-phone"/></svg>(555) 214-3370</li>
      <li><svg class="solid" style="color:var(--firm-red)"><use href="#icon-fax"/></svg>(555) 214-5186</li>
      <li><svg class="solid" style="color:var(--firm-red)"><use href="#icon-phone"/></svg>(888) 431-2059 (Toll-Free)</li>
      <li><svg><use href="#icon-web"/></svg>HarmClaimCounsel.example</li>
    </ul>
  </div>
  <svg class="stripe" viewBox="0 0 552 13" preserveAspectRatio="none" aria-hidden="true">
    <polygon points="0,0 276,0 264,13 0,13" fill="var(--firm-blue)"/>
    <polygon points="276,0 552,0 552,13 264,13" fill="var(--firm-red)"/>
  </svg>
</section>

</body>
</html>
```